Brightmill Data Works

Our company is about IT hardwares and IT solutions. IT hardware such as PC, RAMS, storage and servers. IT solutions such as project management, BA. We are also selling new technology too.

Target Market(s)

Consumer, Small to Medium Business, Corporate

Requirements
Must have
• The business card must have the following:
• Name:
• Title:
• Contact Number:
• Email address:
• Website:
• Color: Must match the logo color upgrade

```html
<!DOCTYPE html>
<html lang="en">
<head>
<meta charset="utf-8">
<title>Brightmill Data Works — Business Card</title>
<link rel="stylesheet" href="https://fonts.googleapis.com/css2?family=Lato:wght@400;700;900&display=swap">
<style>
  :root {
    --backdrop: #2a2a2a;
    --card-dark: #1e1e1e;
    --card-light: #ffffff;
    --accent: #e39a3b;
    --ink-light: #ffffff;
    --ink-dark: #3d3d3d;
    --ink-muted: #d8d8d8;
  }
  * { margin: 0; padding: 0; box-sizing: border-box; }
  html, body {
    width: 1200px; height: 900px; overflow: hidden;
    background: var(--backdrop);
    font-family: "Lato", Arial, sans-serif;
  }
  .stage { position: relative; width: 1200px; height: 900px; }
  .card {
    position: absolute; left: 280px;
    width: 640px; height: 366px;
    background: var(--card-dark);
    overflow: hidden;
    box-shadow: 0 14px 30px rgba(0,0,0,0.45);
  }
  .card--back { top: 60px; }
  .card--front { top: 474px; }

  .brand {
    display: flex; align-items: center; gap: 14px;
    font-weight: 900; text-transform: uppercase;
    letter-spacing: 1px; line-height: 1.05;
  }
  .brand__dot {
    width: 18px; height: 18px; border-radius: 50%;
    background: var(--accent); flex: none;
  }
  .card--back .brand {
    position: absolute; top: 118px; left: 0; right: 0;
    justify-content: center;
    font-size: 36px; color: var(--ink-light);
  }
  .card--back .website {
    position: absolute; bottom: 58px; left: 0; right: 0;
    text-align: center; font-size: 15px; letter-spacing: 0.5px;
    color: var(--ink-light);
  }

  .front-art { position: absolute; inset: 0; }
  .card--front .brand {
    position: absolute; top: 106px; left: 70px;
    font-size: 32px; color: var(--ink-dark);
  }
  .address {
    position: absolute; left: 38px; bottom: 22px;
    font-style: normal;
    font-size: 15px; line-height: 1.35; color: var(--ink-light);
  }
  .contact {
    position: absolute; right: 30px; top: 92px;
    text-align: right; color: var(--ink-light);
  }
  .contact__name { font-size: 22px; font-weight: 700; color: var(--accent); }
  .contact__title { font-size: 13px; margin-bottom: 18px; color: var(--ink-muted); }
  .contact__list { list-style: none; }
  .contact__item {
    display: flex; justify-content: flex-end; align-items: center;
    gap: 8px; font-size: 13.5px; line-height: 1.65;
  }
  .contact__icon { width: 12px; height: 12px; flex: none; }
</style>
</head>
<body>
<main class="stage">

  <section class="card card--back" aria-label="Card back">
    <div class="brand"><span class="brand__dot"></span><span>Brightmill<br>Data Works</span></div>
    <p class="website">www.brightmilldata.com</p>
  </section>

  <section class="card card--front" aria-label="Card front">
    <svg class="front-art" width="640" height="366" viewBox="0 0 640 366" aria-hidden="true">
      <path d="M0,0 H420 C430,170 320,292 0,296 Z" fill="var(--card-light)"/>
      <path d="M432,0 C446,120 404,214 330,272" fill="none" stroke="var(--accent)" stroke-width="5" stroke-linecap="round"/>
    </svg>

    <div class="brand"><span class="brand__dot"></span><span>Brightmill<br>Data Works</span></div>

    <address class="address">418 Alder Crest Road<br>Fairview, OR 97024</address>

    <div class="contact">
      <p class="contact__name">Daniel Hartwell</p>
      <p class="contact__title">Manager</p>
      <ul class="contact__list">
        <li class="contact__item">555 014 2290
          <svg class="contact__icon" viewBox="0 0 12 12"><path d="M2.5 1 L4.5 1 L5.3 3.6 L4 4.6 C4.7 6 6 7.3 7.4 8 L8.4 6.7 L11 7.5 L11 9.5 C11 10.3 10.3 11 9.5 11 C5 11 1 7 1 2.5 C1 1.7 1.7 1 2.5 1 Z" fill="var(--accent)"/></svg>
        </li>
        <li class="contact__item">555 014 2291
          <svg class="contact__icon" viewBox="0 0 12 12"><rect x="3" y="1" width="6" height="3" fill="var(--accent)"/><rect x="1" y="4.5" width="10" height="4.5" rx="1" fill="var(--accent)"/><rect x="3" y="8" width="6" height="3" fill="var(--accent)"/></svg>
        </li>
        <li class="contact__item">hello@brightmilldata.com
          <svg class="contact__icon" viewBox="0 0 12 12"><rect x="0.5" y="2.5" width="11" height="7" fill="var(--accent)"/><path d="M0.5 2.5 L6 6.5 L11.5 2.5" fill="none" stroke="var(--card-dark)" stroke-width="1"/></svg>
        </li>
        <li class="contact__item">www.brightmilldata.com
          <svg class="contact__icon" viewBox="0 0 12 12"><circle cx="6" cy="6" r="5" fill="var(--accent)"/><path d="M1 6 H11 M6 1 C3.5 3.5 3.5 8.5 6 11 M6 1 C8.5 3.5 8.5 8.5 6 11" fill="none" stroke="var(--card-dark)" stroke-width="0.8"/></svg>
        </li>
      </ul>
    </div>
  </section>

</main>
</body>
</html>
```